Book Cover on Entrepreneurship for Eye Doctors

Book Title: The Lens Practice Builder: How to launch with confidence
Author: Rufus Tembley, Optom, MBA, DBA, EIC
I need a Book Cover with the following descriptions:
Topic: the book topic is entrepreneurship knowledge for eye care professionals.
The book's audience: eye care professionals who you know as Opticians, who sell eyeglasses and sunglasses;
Optometrists, test eyes, fit contact lenses, and prescribe medication
Ophthalmologists, perform eye surgery
More about the audience:
1- Young eye care professionals who don’t know about entrepreneurship and those who are stuck in the 9-to-5 job;
2- This is the first book written on entrepreneurship with eye care professionals in mind.
3- Private practice owners the established business guys who are looking to grow their business;
4- Many eye care professionals are MBA holders they may have learned a little bit about entrepreneurship during their MBA studies.
Use the sample cover above and the suggestions that follow as a guide:
1- The cover should be very simple leaving an empty space somewhere to sign the book;
2- The Title and author name should use a modern font;
3- The cover should provide info about what's inside the book through illustrations, for example:
a- Gears: illustrating entrepreneur growth mindset (or anything more explicit)
b- Spectacles, sunglasses, lenses, eye drops, or any other eye care-related correction tools illustrating eye care (or anything more explicit)
c- Symbols illustrating ideas, opportunity, and profit, like money, charts, light bulbs, brain, and coins,...(or anything more explicit)
d- Entrepreneurship illustrated by Briefcase, tie, suit,... (or anything more explicit)

The rest is your creativity and imagination interplay.

Target Market(s)

Eye care professionals: Opticians, Optometrists, Ophthalmologists, Eye Care Administrators, Students in eye specialties.

Industry/Entity Type

eye care

Requirements
Must have
• 1- The cover should be very simple leaving an empty space somewhere to sign the book; 2- The Title and author name should use a modern font; 3- The cover should provide info about what's inside the book through illustrations, for example: a- Gears: illustrating entrepreneur growth mindset (or anything more explicit) b- Spectacles, sunglasses, lenses, eye drops, or any other eye care-related correction tools illustrating eye care (or anything more explicit) c- Symbols illustrating ideas, opportunity, and profit, like money, charts, light bulbs, brain, and coins,...(or anything more explicit) d- Entrepreneurship illustrated by Briefcase, tie, suit,... (or anything more explicit)

```html
<!DOCTYPE html>
<html lang="en">
<head>
<meta charset="utf-8">
<title>The Lens Practice Builder – Full Cover Spread</title>
<link rel="stylesheet" href="https://fonts.googleapis.com/css2?family=Oswald:wght@500;700&family=Montserrat:wght@400;600&display=swap">
<style>
  :root {
    --navy: #14284a;
    --navy-deep: #0e1d38;
    --cyan: #1fa3d8;
    --paper: #ffffff;
    --backdrop: #eef1f5;
    --ink-soft: #3a4a66;
    --body-ink: #4a5568;
    --placeholder: #a9b3c1;
    --photo-light: #dfe9f2;
    --photo-mid: #7fa6c8;
    --photo-dark: #1f3b63;
  }
  html, body {
    margin: 0;
    padding: 0;
    width: 807px;
    height: 1200px;
    overflow: hidden;
    background: var(--backdrop);
  }
  .spread {
    position: absolute;
    left: 0;
    top: 320px;
    width: 807px;
    height: 560px;
    display: flex;
    background: var(--paper);
    box-shadow: 0 4px 18px rgba(14, 29, 56, 0.18);
  }
  .panel {
    position: relative;
    height: 560px;
    background: var(--paper);
    overflow: hidden;
  }
  .back-cover { width: 370px; }
  .spine {
    width: 67px;
    border-left: 1px solid #e3e7ee;
    border-right: 1px solid #e3e7ee;
    box-sizing: border-box;
  }
  .front-cover { width: 370px; }

  .navy-band {
    position: absolute;
    left: 0;
    bottom: 0;
    width: 100%;
    height: 40px;
    background: var(--navy-deep);
  }

  /* Back cover */
  .back-copy {
    position: absolute;
    left: 26px;
    top: 30px;
    width: 318px;
    font-family: "Montserrat", sans-serif;
    font-weight: 400;
    font-size: 10.5px;
    line-height: 1.55;
    color: var(--body-ink);
  }
  .back-copy p { margin: 0 0 12px; }
  .author-bio {
    display: flex;
    gap: 14px;
    margin: 18px 0 14px;
  }
  .author-photo-slot {
    flex: 0 0 96px;
    height: 96px;
    background: var(--placeholder);
  }
  .author-bio p { margin: 0; }

  /* Spine */
  .spine-text {
    position: absolute;
    left: 0;
    top: 18px;
    width: 66px;
    height: 484px;
    writing-mode: vertical-rl;
    transform: rotate(180deg);
    display: flex;
    justify-content: space-between;
    align-items: center;
  }
  .spine-title {
    font-family: "Oswald", sans-serif;
    font-weight: 700;
    font-size: 23px;
    letter-spacing: 0.5px;
    text-transform: uppercase;
    color: var(--navy);
    white-space: nowrap;
  }
  .spine-title .accent { color: var(--cyan); font-weight: 500; }
  .spine-author {
    font-family: "Montserrat", sans-serif;
    font-weight: 600;
    font-size: 8px;
    letter-spacing: 1px;
    text-transform: uppercase;
    color: var(--navy);
    white-space: nowrap;
  }

  /* Front cover */
  .cover-photo {
    position: absolute;
    left: 0;
    top: 0;
    width: 370px;
    height: 225px;
    background:
      radial-gradient(ellipse at 30% 35%, rgba(255,255,255,0.7), transparent 55%),
      radial-gradient(ellipse at 75% 70%, rgba(31,163,216,0.45), transparent 60%),
      linear-gradient(160deg, var(--photo-light) 0%, var(--photo-mid) 55%, var(--photo-dark) 100%);
  }
  .title-block {
    position: absolute;
    left: 30px;
    top: 244px;
    width: 310px;
    margin: 0;
  }
  .title-line {
    display: block;
    font-family: "Oswald", sans-serif;
    font-weight: 700;
    text-transform: uppercase;
    line-height: 0.98;
    letter-spacing: 0.5px;
  }
  .title-main { font-size: 56px; color: var(--navy); }
  .title-accent {
    font-size: 50px;
    color: var(--cyan);
    font-weight: 500;
    letter-spacing: 1px;
  }
  .subtitle {
    position: absolute;
    left: 30px;
    top: 430px;
    margin: 0;
    font-family: "Montserrat", sans-serif;
    font-weight: 600;
    font-size: 10.5px;
    letter-spacing: 1.6px;
    color: var(--ink-soft);
    text-transform: uppercase;
  }
  .author {
    position: absolute;
    left: 30px;
    top: 484px;
    margin: 0;
    font-family: "Montserrat", sans-serif;
    font-weight: 600;
    font-size: 10.5px;
    letter-spacing: 1.2px;
    color: var(--navy);
    text-transform: uppercase;
  }
  .author-rule {
    position: absolute;
    left: 30px;
    top: 504px;
    width: 310px;
    height: 1px;
    background: var(--navy);
  }
</style>
</head>
<body>
  <main class="spread">
    <section class="panel back-cover">
      <div class="back-copy">
        <p>Most eye care professionals train for years to examine, fit and treat, yet few are ever taught how to run a business. This book closes that gap with clear steps for opening, funding and growing a practice of your own.</p>
        <p>Whether you are an optician, optometrist or ophthalmologist, you will learn to read a market, plan your finances, hire a team and build a brand that patients trust.</p>
        <p>Written for young clinicians leaving the nine-to-five and for owners ready to expand, it turns ideas into a practical launch plan.</p>
        <div class="author-bio">
          <div class="author-photo-slot"></div>
          <p>About the author: Rufus Tembley is an optometrist and business educator who has helped clinicians open and grow independent practices.</p>
        </div>
        <p>Practical, direct and built on real clinic experience, this is the guide every eye care professional needs before opening the door.</p>
      </div>
      <div class="navy-band"></div>
    </section>

    <section class="panel spine">
      <div class="spine-text">
        <span class="spine-title">The Lens Practice <span class="accent">Builder</span></span>
        <span class="spine-author">Rufus Tembley, Optom, MBA, DBA, EIC</span>
      </div>
      <div class="navy-band"></div>
    </section>

    <section class="panel front-cover">
      <div class="cover-photo" role="img" aria-label="Photo of hands examining eyeglasses with a glowing growth chart overlay in blue tones"></div>
      <h1 class="title-block">
        <span class="title-line title-main">The Lens</span>
        <span class="title-line title-main">Practice</span>
        <span class="title-line title-accent">Builder</span>
      </h1>
      <p class="subtitle">How to launch with confidence</p>
      <p class="author">Rufus Tembley, Optom, MBA, DBA, EIC</p>
      <div class="author-rule"></div>
      <div class="navy-band"></div>
    </section>
  </main>
</body>
</html>
```